Velmora Nightclub Flyer (Updated)

Flyer for facebook, square is fine, or rectangular. Here is the text:
VELMORA
Nightclub + Lounge
presents

B2B THURSDAY
Nov 29 2018

CLUB FLOOR:
ROLF B2B GARTH
BENEDICT SALVORTE

LOUNGE:
TOBY B2B MY COUSIN
THUNDER REGGIE

Powered by KELP Acoustics
4726 8th Avenue 21+ 9pm-2am
velmorakestrel.com for VIP booth inquiries

Target Market(s)

Nightclub

Industry/Entity Type

Night Club

Font styles to use
Sans Serif

Colors

Designer to choose colors to be used in the design.

Requirements
Must have
• All the text listed, and plz keep the theme of the attached files. We want to stay consistent with the Velmora brand
Nice to have
• Try to stay with the theme from the attachments
Should not have
• Dont' stray to far from the general theme we have from the attachments

```html
<!DOCTYPE html>
<html lang="en">
<head>
<meta charset="utf-8">
<title>Velmora Nightclub + Lounge — B2B Thursday</title>
<link href="https://fonts.googleapis.com/css2?family=Libre+Bodoni:wght@400;700&family=Montserrat:wght@300;400&family=Oswald:wght@500&display=swap" rel="stylesheet">
<style>
  :root {
    --page: #ffffff;
    --silver-light: #e7e8e9;
    --silver-mid: #d3d4d6;
    --silver-dark: #bbbcbf;
    --ink: #231f20;
    --ink-soft: #3a3839;
    --grey-text: #5d5d60;
    --gold: #b98f55;
    --gold-light: #d2ad72;
    --rule: #e9e9ea;
    --label: #ffffff;
  }
  * { margin: 0; padding: 0; box-sizing: border-box; }
  html, body {
    width: 1200px; height: 1162px; overflow: hidden;
    background: var(--page);
  }
  .flyer {
    position: absolute; left: 302px; top: 284px;
    width: 596px; height: 594px; overflow: hidden;
    background: linear-gradient(90deg, var(--silver-light) 0%, var(--silver-mid) 55%, var(--silver-dark) 100%);
  }
  .ornament { position: absolute; left: 0; top: 0; width: 596px; height: 594px; }
  .brand {
    position: absolute; left: 0; top: 82px; width: 100%;
    text-align: center;
    font-family: "Libre Bodoni", serif; font-weight: 400;
    font-size: 64px; line-height: 1; letter-spacing: -1px;
    color: var(--ink);
  }
  .brand-sub {
    position: absolute; left: 0; top: 158px; width: 100%;
    text-align: center;
    font-family: "Montserrat", sans-serif; font-weight: 400;
    font-size: 13px; line-height: 15px; letter-spacing: 3.2px;
    color: var(--ink-soft);
  }
  .date-box {
    position: absolute; left: 298px; top: 265px; width: 57px; height: 25px;
    border: 1px solid var(--gold);
    font-family: "Libre Bodoni", serif; font-size: 14px; line-height: 23px;
    text-align: center; color: var(--gold);
  }
  .event-title {
    position: absolute; left: 364px; top: 267px;
    font-family: "Libre Bodoni", serif; font-weight: 700;
    font-size: 14px; letter-spacing: 0.6px; color: var(--ink);
  }
  .event-rule { position: absolute; left: 364px; top: 286px; width: 170px; height: 6px; }
  .stage-label {
    position: absolute; width: 120px; left: 229px;
    text-align: right;
    font-family: "Oswald", sans-serif; font-weight: 500;
    font-size: 8px; letter-spacing: 1px; line-height: 13px;
    color: var(--label);
  }
  .lineup {
    position: absolute; left: 364px;
    font-family: "Montserrat", sans-serif; font-weight: 400;
    font-size: 10px; line-height: 14px; color: var(--ink);
  }
  .club-floor { top: 314px; }
  .lounge { top: 365px; }
  .info {
    position: absolute; left: 372px; top: 478px; width: 159px;
    border-top: 1px solid var(--rule); border-bottom: 1px solid var(--rule);
    padding: 13px 0 12px;
    font-family: "Montserrat", sans-serif; font-weight: 300;
    font-size: 9.6px; line-height: 10.5px; color: var(--grey-text);
    letter-spacing: -0.1px;
  }
  .info p + p { margin-top: 5px; }
  .info sup { font-size: 6px; line-height: 0; }
</style>
</head>
<body>
  <section class="flyer">
    <svg class="ornament" viewBox="0 0 596 594" role="img" aria-label="Gold mandala ornament rising from the lower left corner">
      <defs>
        <radialGradient id="gold-fill" cx="0" cy="594" r="260" gradientUnits="userSpaceOnUse">
          <stop offset="0" stop-color="#c9a46a" stop-opacity="0.75"/>
          <stop offset="1" stop-color="#c39a5e" stop-opacity="0.45"/>
        </radialGradient>
      </defs>
      <path d="M0,594 L0,342 A252,252 0 0 1 252,594 Z" fill="url(#gold-fill)"/>
    </svg>

    <h1 class="brand">VELMORA</h1>
    <p class="brand-sub">NIGHTCLUB + LOUNGE<br>PRESENTS</p>

    <div class="date-box">NOV 29</div>
    <h2 class="event-title">B2B Thursday</h2>
    <svg class="event-rule" viewBox="0 0 170 6">
      <line x1="0" y1="3" x2="160" y2="3" stroke="var(--gold)" stroke-width="0.8"/>
      <circle cx="164" cy="3" r="2" fill="none" stroke="var(--gold)" stroke-width="0.8"/>
    </svg>

    <p class="stage-label" style="top:314px">CLUB FLOOR:</p>
    <p class="lineup club-floor">ROLF B2B GARTH<br>BENEDICT SALVORTE</p>

    <p class="stage-label" style="top:365px">LOUNGE:</p>
    <p class="lineup lounge">TOBY B2B MY COUSIN<br>THUNDER REGGIE</p>

    <div class="info">
      <p>POWERED BY KELP ACOUSTICS<br>4726 8<sup>TH</sup> AVENUE 21+ 9PM-2AM</p>
      <p>VELMORAKESTREL.COM FOR<br>VIP BOOTH INQUIRIES</p>
    </div>
  </section>
</body>
</html>
```